Corporate Design Hochtemperaturdichtungen
Zielgruppe
Wir sind spezialisiert auf Hochtemperaturdichtungen für den Ofen- & Kaminbau (Ofendichtung).
Desweiteren finden unsere Dichtungen in der Industrie Anwendung (Industrieöfen - Heizkessel
- Lackier- und Trocknungsanlagen - Maschinen- und Anlagenbau)
Die Zielgruppe für unser Angebot von passgenauen Ofendichtungen ist primär der Privatkunde
sowie der Ofenbauer, Kaminstudio / Schornsteinfeger.
Aufgabenstellung
Ziel des Projektes ist die Entwicklung eines neuen Logos-, Visitenkartendesign und damit
verbunden ein Briefpapierdesign für den Brand Glutfalke.
Die Vistitenkarte soll um ein ca. 2x2cm vCard QR-Code ergänzt werden.
Farbwelten:
Für den Brand Glutfalke.de sehe wir tendenziell Feuerfarben :
- rot
- gelb
- orange
- blau
- grün
- grau/schwarz Töne
Bilderwelt:
Prinzipiell möchten wir hier keine Beschränkungen beim Design geben.
Es sollte aber eher ein klares Design sein. Insbesondere wird ein einprägsames Logo in Verbindung
mit dem Markennamen „Glutfalke“ gewünscht. Der Brand soll aber sehr sympathisch und
einprägsam wirken, Wärme und Gebörgenheit ausstrahlen.
Der Rabe sollte sich im neuen Design auch wiederfinden.
Im Idealfall ist das Logo auf einem S/W Laserdrucker druckbar.

```html
<!DOCTYPE html>
<html lang="de">
<head>
<meta charset="utf-8">
<title>Glutfalke – Corporate Design</title>
<link rel="stylesheet" href="https://fonts.googleapis.com/css2?family=Montserrat:wght@400;500;600;700&family=Roboto:wght@300;400&display=swap">
<style>
  :root{
    --navy:#1f3a52;
    --ink:#121e28;
    --orange:#e8541e;
    --board-grey:#4b4b4d;
    --side-grey:#545456;
    --paper:#ffffff;
    --text:#3a3a3a;
  }
  *{margin:0;padding:0;box-sizing:border-box}
  html,body{width:1200px;height:1050px;overflow:hidden;background:var(--side-grey)}
  .board{position:relative;width:1200px;height:1050px;font-family:"Roboto",sans-serif}

  /* brand lockup */
  .lockup{position:absolute;display:flex;flex-direction:column;align-items:center;text-align:center}
  .lockup__name{font-family:"Montserrat",sans-serif;font-weight:700;letter-spacing:-0.02em;line-height:1;color:var(--navy);display:flex;align-items:center;gap:.18em}
  .lockup__dot{display:inline-block;width:.22em;height:.22em;background:var(--orange)}
  .lockup__claim{font-family:"Montserrat",sans-serif;font-weight:400;color:var(--navy);white-space:nowrap;letter-spacing:.01em}
  .lockup--light .lockup__name,.lockup--light .lockup__claim{color:#fff}
  .lockup--dark .lockup__name,.lockup--dark .lockup__claim{color:#2c2c2e}

  /* left column panels */
  .panel{position:absolute;left:0;width:500px}
  .panel--white{top:0;height:350px;background:var(--paper)}
  .panel--grey{top:350px;height:450px;background:var(--board-grey)}
  .panel--ink{top:800px;height:250px;background:var(--ink)}

  .panel--white .lockup{left:0;width:500px;top:158px}
  .panel--white .lockup__name{font-size:50px}
  .panel--white .lockup__claim{font-size:12px;margin-top:8px}
  .panel--ink .lockup{left:0;width:500px;top:98px}
  .panel--ink .lockup__name{font-size:50px}
  .panel--ink .lockup__claim{font-size:12px;margin-top:8px}

  /* business cards */
  .card{position:absolute;left:129px;width:241px;height:156px;box-shadow:0 4px 10px rgba(0,0,0,.35)}
  .card--back{top:53px;background:var(--ink);display:flex;align-items:center;justify-content:center}
  .card--back .card__name{font-family:"Montserrat",sans-serif;font-weight:700;font-size:26px;color:#fff;letter-spacing:-0.02em;display:flex;align-items:center;gap:6px}
  .card--back .card__name i{display:inline-block;width:6px;height:6px;background:var(--orange)}
  .card--front{top:242px;background:var(--paper)}
  .card--front .lockup{left:20px;top:24px;align-items:flex-start}
  .card--front .lockup__name{font-size:29px}
  .card--front .lockup__claim{font-size:7px;margin-top:5px;margin-left:2px}
  .card__bar{position:absolute;left:0;top:96px;width:7px;height:14px;background:var(--orange)}
  .card__person{position:absolute;left:20px;top:95px;font-family:"Montserrat",sans-serif;font-size:5.4px;color:#222;line-height:1.55}
  .card__person strong{font-size:6.8px;font-weight:700;display:block}
  .card__person .addr{margin-top:5px;display:block}
  .card__contacts{position:absolute;left:142px;top:95px;list-style:none;font-family:"Montserrat",sans-serif;font-size:5.4px;color:#222}
  .card__contacts li{display:flex;align-items:center;gap:5px;height:10px}
  .card__contacts svg{width:6px;height:6px;color:var(--orange)}

  /* letterhead */
  .letter{position:absolute;left:553px;top:53px;width:595px;height:842px;background:var(--paper);color:var(--text)}
  .letter .lockup{right:46px;top:55px;align-items:flex-end}
  .letter .lockup__name{font-size:35px}
  .letter .lockup__claim{font-size:8.5px;margin-top:6px}
  .fold{position:absolute;left:0;width:14px;height:0;border-top:1px solid #555}
  .fold--1{top:297px}.fold--2{top:595px}
  .sender{position:absolute;left:74px;top:166px;font-family:"Montserrat",sans-serif;font-size:5.4px;font-weight:500;color:#222}
  .recipient{position:absolute;left:74px;top:181px;font-weight:300;font-size:10px;line-height:12px;color:#333;font-style:normal}
  .letter__body{position:absolute;left:74px;top:294px;width:476px;font-weight:300;font-size:9.6px;line-height:12px;color:#333}
  .letter__body p{margin-bottom:12px}
  .letter__body .salute{margin-bottom:24px}
  .letter__body .closing{margin-top:18px}
  .signature{position:absolute;left:74px;top:603px;width:94px;height:50px;background:linear-gradient(160deg,rgba(29,63,143,.16),rgba(29,63,143,.05));border-radius:3px}
  .letter__foot{position:absolute;left:74px;top:752px;display:flex;font-family:"Montserrat",sans-serif;font-size:6.4px;color:#333}
  .foot__col{list-style:none;padding:0 15px;border-left:1px solid var(--orange);height:67px;padding-top:3px}
  .foot__col:first-child{border-left:none;padding-left:0}
  .foot__col li{height:14px;display:flex;align-items:center;gap:6px;white-space:nowrap}
  .foot__col svg{width:8px;height:8px;color:var(--orange)}
  .foot__col--contact{width:106px}
  .foot__col--person{width:103px}
  .foot__col--bank{width:152px}

  .side-lockup{left:735px;top:940px}
  .side-lockup .lockup__name{font-size:50px}
  .side-lockup .lockup__claim{font-size:12px;margin-top:8px}
</style>
</head>
<body>
<svg width="0" height="0" style="position:absolute" aria-hidden="true">
  <symbol id="ico-phone" viewBox="0 0 16 16"><path d="M4 1.5 6.3 4 5 5.8a9 9 0 0 0 5.2 5.2L12 9.7l2.5 2.3-1.7 2.5C7 14 2 9 1.5 3.2Z" fill="none" stroke="currentColor" stroke-width="1.4" stroke-linejoin="round"/></symbol>
  <symbol id="ico-mobile" viewBox="0 0 16 16"><rect x="4" y="1" width="8" height="14" rx="1.5" fill="none" stroke="currentColor" stroke-width="1.4"/><line x1="7" y1="12.5" x2="9" y2="12.5" stroke="currentColor" stroke-width="1.4"/></symbol>
  <symbol id="ico-fax" viewBox="0 0 16 16"><rect x="1" y="6" width="14" height="8" rx="1" fill="none" stroke="currentColor" stroke-width="1.4"/><rect x="4" y="2" width="8" height="4" fill="none" stroke="currentColor" stroke-width="1.4"/><line x1="4" y1="10" x2="12" y2="10" stroke="currentColor" stroke-width="1.2"/></symbol>
  <symbol id="ico-mail" viewBox="0 0 16 16"><rect x="1" y="3" width="14" height="10" fill="none" stroke="currentColor" stroke-width="1.4"/><path d="M1 3 8 9l7-6" fill="none" stroke="currentColor" stroke-width="1.4"/></symbol>
  <symbol id="ico-web" viewBox="0 0 16 16"><circle cx="8" cy="8" r="6.5" fill="none" stroke="currentColor" stroke-width="1.4"/><ellipse cx="8" cy="8" rx="3" ry="6.5" fill="none" stroke="currentColor" stroke-width="1.2"/><line x1="1.5" y1="8" x2="14.5" y2="8" stroke="currentColor" stroke-width="1.2"/></symbol>
</svg>

<main class="board">
  <section class="panel panel--white">
    <div class="lockup">
      <div class="lockup__name">Glutfalke<span class="lockup__dot"></span></div>
      <div class="lockup__claim">Dichtungen, die jeder Glut sicher standhalten</div>
    </div>
  </section>

  <section class="panel panel--grey">
    <div class="card card--back">
      <div class="card__name">Glutfalke<i></i></div>
    </div>
    <div class="card card--front">
      <div class="lockup">
        <div class="lockup__name">Glutfalke<span class="lockup__dot"></span></div>
        <div class="lockup__claim">Dichtungen, die jeder Glut sicher standhalten</div>
      </div>
      <span class="card__bar"></span>
      <div class="card__person">
        <strong>Max Mustermann</strong>
        Geschäftsführer
        <span class="addr">Musterweg 13<br>54321 Musterdorf</span>
      </div>
      <ul class="card__contacts">
        <li><svg><use href="#ico-phone"/></svg>+49 (0)1234 5 67 89-0</li>
        <li><svg><use href="#ico-mobile"/></svg>+49 (0)1234 5 67 89-50</li>
        <li><svg><use href="#ico-fax"/></svg>+49 (0)123 4 56 78 90</li>
        <li><svg><use href="#ico-mail"/></svg>info@yourcompany.de</li>
        <li><svg><use href="#ico-web"/></svg>yourcompany.de</li>
      </ul>
    </div>
  </section>

  <section class="panel panel--ink">
    <div class="lockup lockup--light">
      <div class="lockup__name">Glutfalke<span class="lockup__dot"></span></div>
      <div class="lockup__claim">Dichtungen, die jeder Glut sicher standhalten</div>
    </div>
  </section>

  <article class="letter">
    <div class="lockup">
      <div class="lockup__name">Glutfalke<span class="lockup__dot"></span></div>
      <div class="lockup__claim">Dichtungen, die jeder Glut sicher standhalten</div>
    </div>
    <span class="fold fold--1"></span>
    <span class="fold fold--2"></span>
    <div class="sender">Your Company | Musterweg 13 | 54321 Musterdorf</div>
    <address class="recipient">Max Mustermann<br>Musterstr. 1<br>12345 Muster</address>
    <div class="letter__body">
      <p class="salute">Sehr geehrte Damen und Herren,</p>
      <p>Lorem ipsum dolor sit amet, consetetur sadipscing elitr, sed diam nonumy eirmod tempor invidunt ut labore et dolore magna aliquyam erat, sed diam voluptua. At vero eos et accusam et justo duo dolores et ea rebum. Stet clita kasd gubergren, no sea takimata sanctus est Lorem ipsum dolor sit amet. Lorem ipsum dolor sit amet, consetetur sadipscing elitr, sed diam nonumy eirmod tempor invidunt ut labore et dolore magna aliquyam erat, sed diam voluptua. At vero eos et accusam et justo duo dolores et ea rebum. Stet clita kasd gubergren, no sea takimata sanctus est Lorem ipsum dolor sit amet. Lorem ipsum dolor sit amet, consetetur sadipscing elitr, sed diam nonumy eirmod tempor invidunt ut labore et dolore magna aliquyam erat, sed diam voluptua. At vero eos et accusam et justo duo dolores et ea rebum. Stet clita kasd gubergren, no sea takimata sanctus est Lorem ipsum dolor sit amet.</p>
      <p>Duis autem vel eum iriure dolor in hendrerit in vulputate velit esse molestie consequat, vel illum dolore eu feugiat nulla facilisis at vero eros et accumsan et iusto odio dignissim qui blandit praesent luptatum zzril delenit augue duis dolore te feugait nulla facilisi. Lorem ipsum dolor sit amet, consectetuer adipiscing elit, sed diam nonummy nibh euismod tincidunt ut laoreet dolore magna aliquam erat volutpat.</p>
      <p>Ut wisi enim ad minim veniam, quis nostrud exerci tation ullamcorper suscipit lobortis nisl ut aliquip ex ea commodo consequat. Duis autem vel eum iriure dolor in hendrerit in vulputate velit esse molestie consequat, vel illum dolore eu feugiat nulla facilisis at vero eros et accumsan et iusto odio dignissim qui blandit praesent luptatum zzril delenit augue duis dolore te feugait nulla facilisi.</p>
      <p class="closing">Mit freundlichen Grüßen</p>
    </div>
    <div class="signature" role="img" aria-label="Handschriftliche Unterschrift"></div>
    <footer class="letter__foot">
      <ul class="foot__col foot__col--contact">
        <li><svg><use href="#ico-phone"/></svg>+49 (0)1234 5 67 89-0</li>
        <li><svg><use href="#ico-fax"/></svg>+49 (0)1234 5 67 89-50</li>
        <li><svg><use href="#ico-mail"/></svg>info@yourcompany.de</li>
        <li><svg><use href="#ico-web"/></svg>yourcompany.de</li>
      </ul>
      <ul class="foot__col foot__col--person">
        <li>MAX MUSTERMANN</li>
        <li>Geschäftsführer</li>
        <li>Musterweg 13</li>
        <li>54321 Musterdorf</li>
      </ul>
      <ul class="foot__col foot__col--bank">
        <li>Stadtbank Nord</li>
        <li>IBAN: DE43 XXXX 0110 XXXX 0481 XX</li>
        <li>BIC: KRXXDE55XXX</li>
        <li>Geschäftsführer: Max Mustermann</li>
      </ul>
      <ul class="foot__col foot__col--legal">
        <li>Ust. ID: DE2XX9XX10X</li>
        <li>HRB 1XX4XX</li>
        <li>Amtsgericht Talbrück</li>
        <li>Gesellschaftssitz: Bachfeld</li>
      </ul>
    </footer>
  </article>

  <div class="lockup lockup--dark side-lockup">
    <div class="lockup__name">Glutfalke<span class="lockup__dot"></span></div>
    <div class="lockup__claim">Dichtungen, die jeder Glut sicher standhalten</div>
  </div>
</main>
</body>
</html>
```